Business Card Design Project

We are a construction company in Orange County, CA. We need a two sided business card. We would like the back to be our logo with web URL. Front should included Name, title, address, phone, fax and email address.

our address is
627 West Dorrance Blvd, Suite 308
Anaheim, CA 92718

Our logo files are attached.

Construction

```html
<!DOCTYPE html>
<html lang="en">
<head>
<meta charset="utf-8">
<title>Arven Business Card</title>
<link href="https://fonts.googleapis.com/css2?family=Source+Sans+3:wght@400;600;700&display=swap" rel="stylesheet">
<style>
  :root{
    --brand-blue:#1d4a7c;
    --brand-blue-light:#3a6596;
    --text-gray:#4a4a4a;
    --card-white:#ffffff;
    --backdrop:#e6e4e1;
  }
  *{margin:0;padding:0;box-sizing:border-box}
  html,body{width:1200px;height:431px;overflow:hidden}
  body{background:var(--backdrop);font-family:"Source Sans 3",Arial,sans-serif;position:relative}
  .card{position:absolute;width:526px;height:301px;background:var(--card-white);border-radius:12px;overflow:hidden;box-shadow:0 2px 6px rgba(0,0,0,.25)}
  .card-front{left:43px;top:60px}
  .card-back{left:588px;top:57px}
  .wordmark{position:absolute;color:var(--brand-blue);font-weight:700;font-size:74px;line-height:1;letter-spacing:-1px}
  .card-front .wordmark{left:56px;top:66px}
  .card-back .wordmark{left:0;right:0;top:110px;text-align:center}
  .contact-list{position:absolute;left:340px;top:69px;list-style:none}
  .contact-list li{display:flex;align-items:center;height:18px;font-size:14px;color:var(--text-gray)}
  .contact-list svg{width:10px;height:10px;margin-right:8px;fill:var(--brand-blue)}
  .address{position:absolute;left:57px;top:178px;font-size:14.5px;line-height:19px;color:var(--text-gray)}
  .wave-band{position:absolute;left:0;right:0;top:226px;bottom:0;background:linear-gradient(180deg,var(--brand-blue-light) 0%,var(--brand-blue) 40%)}
  .person{position:absolute;right:48px;top:243px;text-align:center;color:#fff}
  .person-name{font-weight:700;font-size:17px}
  .person-title{font-size:14px;margin-top:6px;padding-left:6px}
  .back-url{position:absolute;left:0;right:0;top:211px;text-align:center;font-size:14px;letter-spacing:3px;color:var(--text-gray)}
</style>
</head>
<body>
  <section class="card card-front">
    <div class="wordmark">ARVEN</div>
    <ul class="contact-list">
      <li><svg viewBox="0 0 10 10"><path d="M2 0.5 L4 2.5 L3 3.8 Q4.5 6 6.2 7 L7.5 6 L9.5 8 L8 9.5 Q3 9 0.5 2 Z"/></svg>0123 456 789</li>
      <li><svg viewBox="0 0 10 10"><rect x="0.5" y="3" width="9" height="6" rx="1"/><rect x="2.5" y="0.5" width="5" height="3" fill="none" stroke="#1d4a7c"/></svg>0123 456 789</li>
      <li><svg viewBox="0 0 10 10"><rect x="0.5" y="2" width="9" height="6.5"/><path d="M0.5 2 L5 5.5 L9.5 2" fill="none" stroke="#fff" stroke-width="0.8"/></svg>info@arven.com</li>
      <li><svg viewBox="0 0 10 10"><circle cx="5" cy="5" r="4.5"/><path d="M0.5 5 H9.5 M5 0.5 V9.5" fill="none" stroke="#fff" stroke-width="0.6"/></svg>www.arven.com</li>
    </ul>
    <p class="address">627 West Dorrance Blvd<br>Suite 308 Anaheim, CA 92718</p>
    <div class="wave-band" role="img" aria-label="Decorative blue and grey wave band"></div>
    <div class="person">
      <div class="person-name">YOUR NAME</div>
      <div class="person-title">Title</div>
    </div>
  </section>
  <section class="card card-back">
    <div class="wordmark">ARVEN</div>
    <p class="back-url">www.arven.com</p>
  </section>
</body>
</html>
```